Counseling Practice Business Card

I need a professional looking business card incorporating my new logo that was just completed. Card needs to incorporate my name and title, description of my specialty, my address, my phone number, my fax number, my email and my website URL. I need to be able to choose design on/with different paper colors and textures.
I do not have a lot of business card ideas so I am open to anything but I want bold,sharp, clear card without additional designs other than my logo (see attached file info). I am open to different color backgrounds or paper colors including black. I do not like traditional brackets around area codes in phone number or dashes between numbers in phone number. Am open to other ways of presenting including periods between numbers as appropriate. I do not know enough to know what I like yet but I want card to coordinate and work together with my logo. My practice emphasizes natural mental health interventions so any use of color (with background paper color or the blue and green in my logo) that elicits nature is nice. In addition to black, any natural brown or wood looking background might be desirable also. Most of the offerings so far look very similar and boring.

Target Market(s)

Potential therapy clients and other professionals

Contact Information for Business Card

Card information:
Gerald M. Whitcombe, Ph.D.
Licensed Clinical Psychologist
Integrative Health Coach
4812 Marlowe Ridge Blvd SE
Suite 310
Duluth, GA 30096
(770) 415-2983 phone
(770) 581-4096 fax
drgeraldwhitcombe@quillmarsh.net
brightfernwellness.net

Font styles to use
Serif
Sans Serif
Other font styles liked:
• anything that you think looks crisp, clear and easily readable

Requirements
Must have
• Any color used should coordinate with my logo design (see attached files).
• Card should be printed horizontally so top and bottom are longest sides of rectangle.
• Background color or paper color should complement and highlight logo. Do not like a white background. black, grey, brown or any color my logo would blend well with.
Nice to have
• I would like designer to utilize color to highlight letters/name or phone-fax-web symbols.
• Bottom edge of card could be highlighted if appropriate to an idea.
Should not have
• I would NOT want the card to have a pure white background at all.
• No clear cards.
• Cards should be oriented with long sides on bottom and top, NOT sides. DO NOT LIKE THIS THIN TALL ORIENTATION.

```html
<!DOCTYPE html>
<html lang="en">
<head>
<meta charset="utf-8">
<title>Brightfern Counseling – Business Card</title>
<link href="https://fonts.googleapis.com/css2?family=Lato:wght@400;700;900&display=swap" rel="stylesheet">
<style>
  :root {
    --page-bg: #2a2a2a;
    --card-paper: #eef3ec;
    --brand-green: #0a7a3e;
    --brand-blue: #2f78bd;
    --text-light: #ffffff;
  }
  html, body {
    margin: 0;
    padding: 0;
    width: 1200px;
    height: 900px;
    overflow: hidden;
    background: var(--page-bg);
    font-family: "Lato", Arial, sans-serif;
  }
  .card {
    position: absolute;
    left: 100px;
    top: 165px;
    width: 1000px;
    height: 570px;
    border-radius: 28px;
    overflow: hidden;
    background: var(--card-paper);
    box-shadow: 0 18px 40px rgba(0,0,0,0.45);
  }
  .card-bands {
    position: absolute;
    inset: 0;
    width: 100%;
    height: 100%;
  }
  .brand-name {
    position: absolute;
    left: 150px;
    top: 150px;
    margin: 0;
    font-weight: 900;
    font-size: 62px;
    line-height: 1;
    letter-spacing: 0.5px;
    color: var(--brand-green);
  }
  .brand-name .brand-line { display: block; }
  .brand-name .brand-line + .brand-line {
    font-size: 30px;
    letter-spacing: 10px;
    margin-top: 8px;
    margin-left: 4px;
  }
  .holder {
    position: absolute;
    right: 60px;
    top: 292px;
    text-align: right;
    color: var(--text-light);
  }
  .holder-name {
    margin: 0;
    font-size: 26px;
    font-weight: 700;
  }
  .holder-title {
    margin: 4px 0 0;
    font-size: 17px;
    line-height: 1.35;
  }
  .holder-web {
    margin: 10px 0 0;
    font-size: 17px;
    font-weight: 700;
  }
  .contact {
    position: absolute;
    left: 70px;
    top: 382px;
    color: var(--text-light);
    font-size: 17px;
  }
  .contact-list {
    list-style: none;
    margin: 0;
    padding: 0;
  }
  .contact-item {
    display: flex;
    align-items: center;
    gap: 12px;
    height: 25px;
  }
  .contact-icon {
    width: 17px;
    height: 17px;
    fill: var(--text-light);
  }
  .contact-address {
    margin: 10px 0 0;
    font-style: normal;
    font-weight: 700;
    font-size: 18px;
    line-height: 1.35;
  }
</style>
</head>
<body>
  <article class="card">
    <svg class="card-bands" viewBox="0 0 1000 570" preserveAspectRatio="none" aria-hidden="true">
      <path d="M0,350 C350,334 700,222 1000,80 L1000,118 C700,242 350,342 0,356 Z" fill="var(--brand-blue)"/>
      <path d="M0,364 C350,350 700,262 1000,140 L1000,570 L0,570 Z" fill="var(--brand-green)"/>
    </svg>

    <h1 class="brand-name">
      <span class="brand-line">Brightfern</span>
      <span class="brand-line">COUNSELING</span>
    </h1>

    <div class="holder">
      <p class="holder-name">Gerald M. Whitcombe, Ph.D.</p>
      <p class="holder-title">Licensed Clinical Psychologist<br>Integrative Health Coach</p>
      <p class="holder-web">brightfernwellness.net</p>
    </div>

    <div class="contact">
      <ul class="contact-list">
        <li class="contact-item">
          <svg class="contact-icon" viewBox="0 0 24 24" aria-hidden="true"><path d="M6.6 10.8a15 15 0 0 0 6.6 6.6l2.2-2.2c.3-.3.7-.4 1-.2 1.1.4 2.3.6 3.6.6.6 0 1 .4 1 1V20c0 .6-.4 1-1 1A17 17 0 0 1 3 4c0-.6.4-1 1-1h3.5c.6 0 1 .4 1 1 0 1.3.2 2.5.6 3.6.1.3 0 .7-.2 1z"/></svg>
          <span>770.415.2983</span>
        </li>
        <li class="contact-item">
          <svg class="contact-icon" viewBox="0 0 24 24" aria-hidden="true"><path d="M6 3h12v5H6zM4 9h16a2 2 0 0 1 2 2v6h-4v4H6v-4H2v-6a2 2 0 0 1 2-2zm4 7v3h8v-3z"/></svg>
          <span>770.581.4096</span>
        </li>
        <li class="contact-item">
          <svg class="contact-icon" viewBox="0 0 24 24" aria-hidden="true"><path d="M2 5h20v14H2zm2 2v.5l8 5 8-5V7zm0 2.8V17h16V9.8l-8 5z"/></svg>
          <span>drgeraldwhitcombe@quillmarsh.net</span>
        </li>
      </ul>
      <address class="contact-address">
        4812 Marlowe Ridge Blvd SE<br>
        Suite 310, Duluth, GA 30096
      </address>
    </div>
  </article>
</body>
</html>
```